Super elegant, crisp & clean Business card design required

We recently upgraded our branding - which is on our website - talvendoraphoto.com

I would like a simple, yet elegant, clean business card design please.

The font of my logo is Cinzel - and because of the natural colour - it's best to have this on a black background.

I would like to have the back of the business card - with simply my logo.

PLEASE DO NOT SUBMIT A COMPLICATED / UNCLEAN DESIGN

Industry/Entity Type

Business

Contact Information for Business Card

Talven Doroshko Photography

Font styles to use
Other font styles liked:
• Cinzel

Requirements
Must have
• A backpage with nothing but my logo
• Simple design - stands out
Should not have
• Colour that dont align with my logo
• Over complicated '/ non symmetrical design

```html
<!DOCTYPE html>
<html lang="en">
<head>
<meta charset="utf-8">
<title>Talven Doroshko Photography – Business Card</title>
<link rel="stylesheet" href="https://fonts.googleapis.com/css2?family=Cinzel:wght@400&family=Open+Sans:wght@400;600&display=swap">
<style>
  :root {
    --stage: #ecebe8;
    --card: #ffffff;
    --brand: #7a6d58;
    --brand-soft: rgba(122, 109, 88, 0.14);
    --ink: #5a5a5a;
  }
  * { margin: 0; padding: 0; box-sizing: border-box; }
  html, body { width: 1200px; height: 900px; overflow: hidden; }
  body {
    background: var(--stage);
    position: relative;
    font-family: "Open Sans", Arial, sans-serif;
  }
  .card {
    position: absolute;
    background: var(--card);
    box-shadow: 0 6px 18px rgba(0, 0, 0, 0.12);
    overflow: hidden;
  }
  .card--front { left: 238px; top: 61px; width: 555px; height: 344px; }
  .card--back  { left: 457px; top: 519px; width: 560px; height: 342px; }

  .front-accent { position: absolute; left: 0; top: 0; width: 555px; height: 344px; }

  .holder { position: absolute; left: 38px; top: 40px; }
  .holder__name { color: var(--brand); font-weight: 600; font-size: 19px; line-height: 1.2; }
  .holder__role { color: var(--ink); font-size: 15px; line-height: 1.2; }

  .address {
    position: absolute; left: 38px; top: 168px;
    color: var(--ink); font-size: 15px; line-height: 20px;
    font-style: normal;
  }
  .contact-list {
    position: absolute; left: 38px; top: 223px;
    list-style: none; color: var(--ink); font-size: 15px; line-height: 20px;
  }
  .contact-list li { display: flex; align-items: center; gap: 8px; }
  .contact-list svg { width: 11px; height: 11px; fill: var(--ink); flex: none; }

  .brand-mark {
    position: absolute; left: 0; right: 0; top: 0; bottom: 0;
    display: flex; flex-direction: column; align-items: center; justify-content: center;
    padding-top: 110px;
    font-family: "Cinzel", Georgia, serif; font-weight: 400; color: var(--brand);
  }
  .brand-mark__dot {
    width: 14px; height: 14px; border-radius: 50%; background: var(--brand);
    margin-bottom: 70px;
  }
  .brand-mark__name { font-size: 27px; letter-spacing: 0.5px; line-height: 1; }
  .brand-mark__tag { font-size: 13px; letter-spacing: 6px; margin-top: 6px; line-height: 1; }
</style>
</head>
<body>
  <section class="card card--front" aria-label="Card front">
    <svg class="front-accent" viewBox="0 0 555 344" role="img" aria-label="Flowing script initial ornament">
      <rect x="374" y="8" width="84" height="282" rx="40" fill="var(--brand-soft)"/>
    </svg>
    <svg class="front-accent" viewBox="0 0 555 344" aria-hidden="true">
      <polygon class="chevron__upper" points="427,0 555,0 555,166" fill="var(--brand)"/>
      <polygon class="chevron__lower" points="434,344 555,344 555,180" fill="var(--brand)"/>
      <line class="chevron__stripe" x1="441" y1="0" x2="555" y2="148" stroke="#ffffff" stroke-width="3"/>
      <line class="chevron__stripe" x1="448" y1="344" x2="555" y2="198" stroke="#ffffff" stroke-width="3"/>
    </svg>

    <div class="holder">
      <p class="holder__name">Elias Marrow</p>
      <p class="holder__role">Managing Director</p>
    </div>

    <address class="address">12345, Address Goes Here<br>Country Name, 123456.</address>

    <ul class="contact-list">
      <li><svg viewBox="0 0 12 12"><path d="M2.5 0.5l2 2-1 1.5c.6 1.5 2 3 3.5 3.5l1.5-1 2 2-1.2 1.8C5 9.8 2.2 7 .8 1.7z"/></svg>044-555 018 240</li>
      <li><svg viewBox="0 0 12 12"><path d="M3 0h6v3H3zM1 4h10v6H9v2H3v-2H1zM4 8v3h4V8z"/></svg>044-555 018 240</li>
      <li><svg viewBox="0 0 12 12"><path d="M0 2h12v1L6 7 0 3zM0 4.5l6 4 6-4V10H0z"/></svg>info@talvendoraphoto.com</li>
      <li><svg viewBox="0 0 12 12"><circle cx="6" cy="6" r="5.5"/></svg>www.talvendoraphoto.com</li>
    </ul>
  </section>

  <section class="card card--back" aria-label="Card back">
    <div class="brand-mark">
      <span class="brand-mark__dot" aria-hidden="true"></span>
      <p class="brand-mark__name">Talven Doroshko</p>
      <p class="brand-mark__tag">PHOTOGRAPHY</p>
    </div>
  </section>
</body>
</html>
```